flat share room mate rental website(design only)

We need a design for the homepage of a flat share / roommate website. We have a website template http://demo1.nestvaleprops.net and we're looking for a homepage similar to this http://uk.bunkmatchly.com but different.
The main user of the site are likely to be students and young professionals so were not looking for anything too serious.
We want to emphasise that the website will be 100% free to use both to post an advert and to contact the advertiser.
We must have a 'new rooms' and new flatmates carousel, also we would prefer if the menu had only a login button and maybe a 'post a room' button.
Our logo is currently being designed, so you can put anything in its place.
We look forward to seeing what you guys come up with.
Target Market(s)
Students, Young Professionals
Industry/Entity Type
Rental
Number of Pages Required
1 page
Look and feel
Each slider illustrates characteristics of the customer's brand and the style your logo design should communicate.

```html
<!DOCTYPE html>
<html lang="en">
<head>
<meta charset="utf-8">
<title>Flatshare Homepage</title>
<link href="https://fonts.googleapis.com/css2?family=Oswald:wght@400;500&family=Open+Sans:wght@400;600;700&display=swap" rel="stylesheet">
<style>
:root{
  --teal:#8dd3c7;
  --teal-dark:#74c2b5;
  --orange:#f7a53f;
  --pink:#f48f97;
  --sky:#8ec9e6;
  --ink:#2b2b2b;
  --text:#555;
  --muted:#8a8a8a;
  --band:#e9e9e9;
  --footer:#2a2a2a;
  --footer-text:#a8a8a8;
  --white:#fff;
}
*{box-sizing:border-box;margin:0;padding:0}
html,body{width:1200px;height:3090px;overflow:hidden}
body{font-family:"Open Sans",Arial,sans-serif;color:var(--text);background:var(--white);position:relative}
.heading{font-family:"Oswald",Arial,sans-serif;font-weight:400;text-transform:uppercase;color:var(--ink)}
section,header,footer{position:absolute;left:0;width:1200px}

/* top bar + hero */
.topbar{top:0;height:44px;background:var(--teal);z-index:2;display:flex;align-items:center;justify-content:space-between;padding:0 72px}
.logo{font-family:"Oswald",Arial,sans-serif;font-size:22px;color:var(--white);letter-spacing:.5px}
.nav a{color:var(--white);font-size:13px;text-decoration:none;margin-left:26px;text-transform:uppercase}
.hero{top:0;height:640px}
.hero-photo{position:absolute;inset:0;background:linear-gradient(115deg,#6b6f6c 0%,#9a9690 30%,#5c524b 55%,#3f3833 80%,#2e2925 100%)}
.hero-shade{position:absolute;inset:0;background:rgba(0,0,0,.25)}
.hero-title{position:absolute;top:232px;width:100%;text-align:center;color:var(--white);font-size:44px}
.search{position:absolute;top:350px;left:206px;width:772px;height:66px;background:rgba(255,255,255,.22);display:flex;align-items:center;padding:0 14px;gap:18px}
.select{width:400px;height:36px;background:var(--white);border-radius:2px;font-size:13px;color:#888;display:flex;align-items:center;justify-content:space-between;padding:0 14px}
.btn{height:36px;display:inline-flex;align-items:center;justify-content:center;font-family:"Oswald",Arial,sans-serif;font-size:15px;color:var(--white);text-transform:uppercase;border-radius:2px;letter-spacing:.3px}
.btn-orange{background:var(--orange)}
.btn-pink{background:var(--pink)}
.search .btn{width:160px}
.hero-note{position:absolute;top:432px;width:100%;text-align:center;color:var(--white);font-family:"Oswald",Arial,sans-serif;font-size:17px;line-height:28px;text-transform:uppercase}
.hero-note b{color:var(--orange);font-weight:400}

/* card rows */
.row-head{position:absolute;left:72px;right:72px;display:flex;justify-content:space-between;align-items:center}
.row-head .heading{font-size:24px}
.arrows{display:flex;gap:6px}
.arrow{width:24px;height:24px;border-radius:3px;display:flex;align-items:center;justify-content:center}
.arrow.off{background:#c9c9c9}
.arrow.on-orange{background:var(--orange)}
.arrow.on-sky{background:var(--sky)}
.arrow.on-teal{background:var(--teal)}
.cards{position:absolute;left:72px;display:flex;gap:25px}
.card{width:245px}
.card-photo{height:134px}
.strip{height:25px;display:flex;align-items:center;justify-content:space-between;padding:0 8px;color:var(--white);font-size:12px}
.strip span{display:flex;align-items:center;gap:5px}
.strip b{font-size:14px}
.strip-orange{background:var(--orange)}
.strip-sky{background:var(--sky)}
.strip-teal{background:var(--teal)}
.card p{font-size:13px;line-height:19px;margin-top:12px;padding-right:6px}

/* stats band */
.stats{top:1038px;height:412px;background:var(--band)}
.stats .title{position:absolute;top:84px;width:100%;text-align:center;font-size:24px}
.feature{position:absolute;top:140px;width:340px;text-align:center}
.feature .circle{width:122px;height:122px;border-radius:50%;background:var(--white);margin:0 auto;display:flex;align-items:center;justify-content:center}
.feature h3{font-family:"Open Sans",Arial,sans-serif;font-weight:700;font-size:16px;color:var(--ink);margin-top:30px;text-transform:uppercase}
.feature p{font-size:13px;line-height:19px;margin-top:14px}

/* banner */
.banner{top:1850px;height:230px;background:linear-gradient(100deg,#4a2d2a 0%,#7a3b33 35%,#8a4a3c 55%,#5a3a35 80%,#3c2b2b 100%)}
.banner-text{position:absolute;top:58px;width:100%;text-align:center;color:var(--white);font-size:48px;line-height:50px}

/* call to action */
.cta{top:2480px;height:180px;background:var(--band)}
.cta .title{position:absolute;top:40px;width:100%;text-align:center;font-size:24px}
.cta-buttons{position:absolute;top:98px;left:397px;display:flex;gap:10px}
.cta-buttons .btn{width:200px;height:38px}

/* footer */
.footer{top:2660px;height:430px;background:var(--footer);color:var(--footer-text)}
.fcol{position:absolute;top:48px;width:250px}
.fcol h4{font-family:"Open Sans",Arial,sans-serif;font-weight:700;font-size:13px;color:var(--white);text-transform:uppercase;margin-bottom:10px}
.fcol li{list-style:none;font-size:13px;line-height:22px}
.fcol .all{color:var(--white);font-weight:600;margin-top:12px}
.social{display:flex;gap:6px;margin-top:4px}
.social i{width:26px;height:26px;border:1.5px solid #777;border-radius:50%;display:block}
.legal{position:absolute;top:378px;left:72px;right:72px;display:flex;justify-content:space-between;font-size:12px}
.legal span+span{margin-left:18px}
</style>
</head>
<body>

<header class="topbar">
  <div class="logo">LOGO HERE</div>
  <nav class="nav"><a href="#">Login</a><a href="#">Post a Room</a></nav>
</header>

<section class="hero">
  <div class="hero-photo" role="img" aria-label="Bright modern loft bedroom with sofa, bed and striped wall"></div>
  <div class="hero-shade"></div>
  <h1 class="heading hero-title" style="color:var(--white)">Find your perfect flatmate</h1>
  <div class="search">
    <div class="select">Select a location
      <svg width="12" height="8" viewBox="0 0 12 8"><path d="M1 1l5 5 5-5" fill="none" stroke="#999" stroke-width="1.8"/></svg>
    </div>
    <span class="btn btn-orange">I need a room</span>
    <span class="btn btn-pink">I have a room</span>
  </div>
  <p class="hero-note"><b>No fees.</b> We don't charge you anything.<br>That means no fees to post an advert and no fees to contact your potential new flatmate.</p>
</section>

<!-- new rooms -->
<section style="top:640px;height:398px">
  <div class="row-head" style="top:42px">
    <h2 class="heading">New rooms to rent</h2>
    <div class="arrows">
      <span class="arrow off"><svg width="8" height="12"><path d="M6 1L2 6l4 5" fill="none" stroke="#fff" stroke-width="2"/></svg></span>
      <span class="arrow on-orange"><svg width="8" height="12"><path d="M2 1l4 5-4 5" fill="none" stroke="#fff" stroke-width="2"/></svg></span>
    </div>
  </div>
  <div class="cards" style="top:94px">
    <article class="card"><div class="card-photo" role="img" aria-label="Warm bedroom with wooden furniture" style="background:linear-gradient(135deg,#8a5a2e,#3a2a20)"></div>
      <div class="strip strip-orange"><span><svg width="10" height="13" viewBox="0 0 10 13"><path d="M5 12S1 7 1 4.5a4 4 0 018 0C9 7 5 12 5 12z" fill="#fff"/></svg>Wolverhampton</span><b>£250</b></div>
      <p>In publishing and graphic design, lorem ipsum is a filler text commonly used to demonstrate the graphic elements of a document or visual presentation.</p></article>
    <article class="card"><div class="card-photo" role="img" aria-label="Colourful student room with desk and pink chair" style="background:linear-gradient(135deg,#d8c9a8,#b8a27e)"></div>
      <div class="strip strip-orange"><span><svg width="10" height="13" viewBox="0 0 10 13"><path d="M5 12S1 7 1 4.5a4 4 0 018 0C9 7 5 12 5 12z" fill="#fff"/></svg>Wolverhampton</span><b>£250</b></div>
      <p>In publishing and graphic design, lorem ipsum is a filler text commonly used to demonstrate the graphic elements of a document or visual presentation.</p></article>
    <article class="card"><div class="card-photo" role="img" aria-label="Grey bedroom with tall windows" style="background:linear-gradient(135deg,#b7bcc0,#6f7478)"></div>
      <div class="strip strip-orange"><span><svg width="10" height="13" viewBox="0 0 10 13"><path d="M5 12S1 7 1 4.5a4 4 0 018 0C9 7 5 12 5 12z" fill="#fff"/></svg>Wolverhampton</span><b>£250</b></div>
      <p>In publishing and graphic design, lorem ipsum is a filler text commonly used to demonstrate the graphic elements of a document or visual presentation.</p></article>
    <article class="card"><div class="card-photo" role="img" aria-label="Light bedroom with white bed" style="background:linear-gradient(135deg,#efe9e2,#c9b9a6)"></div>
      <div class="strip strip-orange"><span><svg width="10" height="13" viewBox="0 0 10 13"><path d="M5 12S1 7 1 4.5a4 4 0 018 0C9 7 5 12 5 12z" fill="#fff"/></svg>Wolverhampton</span><b>£250</b></div>
      <p>In publishing and graphic design, lorem ipsum is a filler text commonly used to demonstrate the graphic elements of a document or visual presentation.</p></article>
  </div>
</section>

<section class="stats">
  <h2 class="heading title">5,456,267 happy flatshares and counting...</h2>
  <div class="feature" style="left:70px">
    <div class="circle"><svg width="40" height="54" viewBox="0 0 40 54"><path d="M20 51S4 31 4 19a16 16 0 0132 0c0 12-16 32-16 32z" fill="none" stroke="var(--orange)" stroke-width="3"/><circle cx="20" cy="19" r="6" fill="none" stroke="var(--orange)" stroke-width="3"/></svg></div>
    <h3>Great rooms</h3>
    <p>In publishing and graphic design, lorem ipsum is a filler text commonly used to demonstrate the graphic elements of a document or visual presentation.</p>
  </div>
  <div class="feature" style="left:430px">
    <div class="circle"><svg width="50" height="50" viewBox="0 0 50 50"><circle cx="20" cy="20" r="14" fill="none" stroke="var(--sky)" stroke-width="3"/><path d="M30 30l14 14" stroke="var(--sky)" stroke-width="4" stroke-linecap="round"/></svg></div>
    <h3>Easy search</h3>
    <p>In publishing and graphic design, lorem ipsum is a filler text commonly used to demonstrate the graphic elements of a document or visual presentation.</p>
  </div>
  <div class="feature" style="left:790px">
    <div class="circle"><svg width="54" height="48" viewBox="0 0 54 48"><path d="M14 4h36v24H34l-6 6v-6H14z" fill="none" stroke="var(--teal-dark)" stroke-width="3"/><path d="M10 14H4v22h6v8l8-8h16v-4" fill="none" stroke="var(--teal-dark)" stroke-width="3"/><path d="M21 12h22M21 18h22" stroke="var(--teal-dark)" stroke-width="2.5"/></svg></div>
    <h3>Expert help 24/7</h3>
    <p>In publishing and graphic design, lorem ipsum is a filler text commonly used to demonstrate the graphic elements of a document or visual presentation.</p>
  </div>
</section>

<!-- community -->
<section style="top:1450px;height:400px">
  <div class="row-head" style="top:44px">
    <h2 class="heading">Our community</h2>
    <div class="arrows">
      <span class="arrow off"><svg width="8" height="12"><path d="M6 1L2 6l4 5" fill="none" stroke="#fff" stroke-width="2"/></svg></span>
      <span class="arrow on-sky"><svg width="8" height="12"><path d="M2 1l4 5-4 5" fill="none" stroke="#fff" stroke-width="2"/></svg></span>
    </div>
  </div>
  <div class="cards" style="top:95px">
    <article class="card"><div class="card-photo" role="img" aria-label="Portrait of a smiling student" style="background:linear-gradient(135deg,#c9a77a,#7d6048)"></div>
      <div class="strip strip-sky"><span>Chris</span><span>16-Sep-2014</span></div>
      <p>In publishing and graphic design, lorem ipsum is a filler text commonly used to demonstrate the graphic elements of a document or visual presentation.</p></article>
    <article class="card"><div class="card-photo" role="img" aria-label="Portrait of a student in a library" style="background:linear-gradient(135deg,#a26c52,#5b4036)"></div>
      <div class="strip strip-sky"><span>Jack</span><span>18-Aug-2014</span></div>
      <p>In publishing and graphic design, lorem ipsum is a filler text commonly used to demonstrate the graphic elements of a document or visual presentation.</p></article>
    <article class="card"><div class="card-photo" role="img" aria-label="Portrait of a young person in a library" style="background:linear-gradient(135deg,#9a7658,#4f3e33)"></div>
      <div class="strip strip-sky"><span>Laura</span><span>12-Sep-2014</span></div>
      <p>In publishing and graphic design, lorem ipsum is a filler text commonly used to demonstrate the graphic elements of a document or visual presentation.</p></article>
    <article class="card"><div class="card-photo" role="img" aria-label="Portrait of a smiling young professional" style="background:linear-gradient(135deg,#b9c6d0,#5f6c78)"></div>
      <div class="strip strip-sky"><span>John</span><span>12-Sep-2014</span></div>
      <p>In publishing and graphic design, lorem ipsum is a filler text commonly used to demonstrate the graphic elements of a document or visual presentation.</p></article>
  </div>
</section>

<section class="banner" role="img" aria-label="Friends holding hands at sunset">
  <h2 class="heading banner-text" style="color:var(--white)">Helping you find a flatshare<br>you can call home</h2>
</section>

<!-- new flatmates -->
<section style="top:2080px;height:400px">
  <div class="row-head" style="top:45px">
    <h2 class="heading">New flatmates</h2>
    <div class="arrows">
      <span class="arrow off"><svg width="8" height="12"><path d="M6 1L2 6l4 5" fill="none" stroke="#fff" stroke-width="2"/></svg></span>
      <span class="arrow on-teal"><svg width="8" height="12"><path d="M2 1l4 5-4 5" fill="none" stroke="#fff" stroke-width="2"/></svg></span>
    </div>
  </div>
  <div class="cards" style="top:98px">
    <article class="card"><div class="card-photo" role="img" aria-label="Two friends in winter hats" style="background:linear-gradient(135deg,#a9b4c0,#6b4a5c)"></div>
      <div class="strip strip-teal"><span><svg width="12" height="12" viewBox="0 0 12 12"><circle cx="6" cy="3.5" r="2.8" fill="#fff"/><path d="M0.5 12a5.5 5 0 0111 0z" fill="#fff"/></svg>Lorem Ipsu 31</span></div>
      <p>In publishing and graphic design, lorem ipsum is a filler text commonly used to demonstrate the graphic elements of a document or visual presentation.</p></article>
    <article class="card"><div class="card-photo" role="img" aria-label="Flatmates relaxing on a sofa" style="background:linear-gradient(135deg,#7a6a5a,#3a3430)"></div>
      <div class="strip strip-teal"><span><svg width="12" height="12" viewBox="0 0 12 12"><circle cx="6" cy="3.5" r="2.8" fill="#fff"/><path d="M0.5 12a5.5 5 0 0111 0z" fill="#fff"/></svg>Lorem Ipsu 31</span></div>
      <p>In publishing and graphic design, lorem ipsum is a filler text commonly used to demonstrate the graphic elements of a document or visual presentation.</p></article>
    <article class="card"><div class="card-photo" role="img" aria-label="Group of friends outdoors" style="background:linear-gradient(135deg,#c8d6dc,#b08a66)"></div>
      <div class="strip strip-teal"><span><svg width="12" height="12" viewBox="0 0 12 12"><circle cx="6" cy="3.5" r="2.8" fill="#fff"/><path d="M0.5 12a5.5 5 0 0111 0z" fill="#fff"/></svg>Lorem Ipsu 31</span></div>
      <p>In publishing and graphic design, lorem ipsum is a filler text commonly used to demonstrate the graphic elements of a document or visual presentation.</p></article>
    <article class="card"><div class="card-photo" role="img" aria-label="Friends lying on the floor together" style="background:linear-gradient(135deg,#d9e4ec,#9fb2c2)"></div>
      <div class="strip strip-teal"><span><svg width="12" height="12" viewBox="0 0 12 12"><circle cx="6" cy="3.5" r="2.8" fill="#fff"/><path d="M0.5 12a5.5 5 0 0111 0z" fill="#fff"/></svg>Lorem Ipsu 31</span></div>
      <p>In publishing and graphic design, lorem ipsum is a filler text commonly used to demonstrate the graphic elements of a document or visual presentation.</p></article>
  </div>
</section>

<section class="cta">
  <h2 class="heading title">Find your perfect flatshare today!</h2>
  <div class="cta-buttons">
    <span class="btn btn-orange">Start your search</span>
    <span class="btn btn-pink">Post your room</span>
  </div>
</section>

<footer class="footer">
  <div class="fcol" style="left:72px">
    <h4>Popular cities</h4>
    <ul>
      <li>Birmingham flatshare</li><li>Bristol flatshare</li><li>Coventry flatshare</li><li>Leeds flatshare</li><li>Liverpool flatshare</li><li>London flatshare</li><li>Manchester flatshare</li><li>Newcastle upon Tyne flatshare</li><li>Nottingham flatshare</li><li>Sheffield flatshare</li>
      <li class="all">All cities</li>
    </ul>
  </div>
  <div class="fcol" style="left:342px">
    <h4>Flatshare types</h4>
    <ul>
      <li>Bedsits And Studios</li><li>Double Room Flatshare</li><li>DSS</li><li>Female Flatshare</li><li>Monday to Friday</li><li>Professional Flatshare</li><li>Roomshare</li><li>Short Let</li><li>Single Room Flatshare</li><li>Spareroom And Lodger</li><li>Student Accommodation</li>
    </ul>
  </div>
  <div class="fcol" style="left:613px">
    <h4>About us</h4>
    <ul>
      <li>Need help?</li><li>FAQs</li><li>Press Room</li><li>Website Visitor &amp; User Agreements</li><li>Right-To-Rent</li><li>Become an Affiliate</li><li>Our Pledge</li>
    </ul>
  </div>
  <div class="fcol" style="left:883px">
    <h4>Discover</h4>
    <ul><li>Landlord Zone</li><li>Our Blog</li></ul>
    <h4 style="margin-top:24px">Stay connected</h4>
    <div class="social"><i></i><i></i><i></i><i></i><i></i></div>
  </div>
  <div class="legal">
    <span>©2015 - Cmpany Name here. All Rights Reserved.</span>
    <span><span>Privacy Policy</span><span>Terms of Use</span></span>
  </div>
</footer>

</body>
</html>
```